Animal Eye Clinic needs a Business card

We are a new veterinary ophthalmology practice (Ridgeline Pet Vision Care) and we need a business card designed. We only see animal eyes - we are not a regular veterinary clinic. We already have a logo. We are looking for a professional, good looking business card to hand out to our clients. We are looking for something simple but professional and contemporary. Our logo is likely the only picture/graphic that needs to be on the card.
Updates

Contact Information for Business Card

Delia Vossman, BSc, DVM, MSc, DipACVO
Veterinary Ophthalmologist

Phone: 250.418.3927
Email: ridgelinepetvisioncare@mailbox-example.net
Website: ridgelinepetvisioncare-example.net
Address: 1874 Thornbury Rd
Kelowna, BC, V1X 4M9

Colors

Designer to choose colors to be used in the design.

Requirements
Must have
• Our logo (attached)

```html
<!DOCTYPE html>
<html lang="en">
<head>
<meta charset="utf-8">
<title>Ridgeline Pet Vision Care – Business Card</title>
<link rel="stylesheet" href="https://fonts.googleapis.com/css2?family=Montserrat:wght@400;500;600;700&display=swap">
<style>
  :root {
    --teal: #1c99a8;
    --swoosh-grey: #6f6f70;
    --white: #ffffff;
    --backdrop: #5b5b5b;
    --font: "Montserrat", Arial, sans-serif;
  }
  * { margin: 0; padding: 0; box-sizing: border-box; }
  html, body {
    width: 1200px; height: 1200px; overflow: hidden;
    background: var(--backdrop);
    font-family: var(--font);
  }
  .canvas { position: relative; width: 1200px; height: 1200px; }
  .card {
    position: absolute; left: 200px;
    width: 800px; height: 461px;
    border-radius: 18px; overflow: hidden;
    background: var(--teal); color: var(--white);
  }
  .card--front { top: 92px; }
  .card--back { top: 646px; }

  .front-shape { position: absolute; inset: 0; width: 800px; height: 461px; }

  .contact { position: absolute; left: 42px; top: 0; }
  .contact > * { position: absolute; left: 0; white-space: nowrap; }
  .contact__name { top: 86px; font-size: 26px; font-weight: 700; letter-spacing: 0.5px; text-transform: uppercase; }
  .contact__credentials { top: 124px; font-size: 13px; font-weight: 400; }
  .contact__title { top: 146px; font-size: 18px; font-weight: 500; }
  .contact__rule { width: 150px; height: 2px; background: var(--white); }
  .contact__rule--one { top: 194px; }
  .contact__rule--two { top: 264px; }
  .contact__address { top: 206px; font-size: 17px; font-weight: 400; line-height: 24px; }
  .contact__line { display: flex; align-items: center; gap: 10px; font-size: 17px; font-weight: 500; }
  .contact__line--phone { top: 280px; }
  .contact__line--email { top: 312px; font-size: 14px; }
  .contact__line--web { top: 343px; font-size: 15px; }
  .contact__icon { width: 12px; height: 12px; flex: none; }

  .brand { position: absolute; display: flex; align-items: center; gap: 16px; }
  .brand__dot { border-radius: 50%; flex: none; }
  .brand__name { font-weight: 700; text-transform: uppercase; line-height: 1.1; }
  .brand--front { left: 460px; top: 192px; color: var(--teal); }
  .brand--front .brand__dot { width: 70px; height: 70px; background: var(--teal); }
  .brand--front .brand__name { font-size: 26px; }
  .brand--back { left: 50%; top: 50%; transform: translate(-50%, -50%); color: var(--white); }
  .brand--back .brand__dot { width: 110px; height: 110px; background: var(--white); }
  .brand--back .brand__name { font-size: 40px; }
</style>
</head>
<body>
<main class="canvas">

  <section class="card card--front" aria-label="Business card front">
    <svg class="front-shape" viewBox="0 0 800 461" aria-hidden="true">
      <path fill="var(--swoosh-grey)" d="M735,0 C560,60 425,150 400,232 C430,330 565,410 735,461 L800,461 L800,0 Z"/>
      <path fill="var(--white)" d="M765,0 C605,70 445,160 422,232 C452,322 605,400 765,461 L800,461 L800,0 Z"/>
    </svg>

    <div class="contact">
      <h1 class="contact__name">Delia Vossman</h1>
      <p class="contact__credentials">BSc, DVM, MSc, DipACVO</p>
      <p class="contact__title">Veterinary Ophthalmologist</p>
      <span class="contact__rule contact__rule--one"></span>
      <p class="contact__address">1874 Thornbury Rd<br>Kelowna, BC, V1X 4M9</p>
      <span class="contact__rule contact__rule--two"></span>
      <p class="contact__line contact__line--phone">
        <svg class="contact__icon" viewBox="0 0 24 24" aria-hidden="true"><path fill="#fff" d="M6.6 10.8a15.1 15.1 0 0 0 6.6 6.6l2.2-2.2c.3-.3.7-.4 1-.2 1.1.4 2.3.6 3.6.6.6 0 1 .4 1 1V20c0 .6-.4 1-1 1A17 17 0 0 1 3 4c0-.6.4-1 1-1h3.5c.6 0 1 .4 1 1 0 1.3.2 2.5.6 3.6.1.3 0 .7-.2 1z"/></svg>
        250.418.3927
      </p>
      <p class="contact__line contact__line--email">
        <svg class="contact__icon" viewBox="0 0 24 24" aria-hidden="true"><path fill="#fff" d="M2 5h20v14H2z"/><path fill="none" stroke="var(--teal)" stroke-width="2" d="M3 6l9 7 9-7"/></svg>
        ridgelinepetvisioncare@mailbox-example.net
      </p>
      <p class="contact__line contact__line--web">
        <svg class="contact__icon" viewBox="0 0 24 24" aria-hidden="true"><circle cx="12" cy="12" r="10" fill="#fff"/><path fill="none" stroke="var(--teal)" stroke-width="1.6" d="M2 12h20M12 2c3 3 3 17 0 20M12 2c-3 3-3 17 0 20"/></svg>
        www.ridgelinepetvisioncare-example.net
      </p>
    </div>

    <div class="brand brand--front">
      <span class="brand__dot"></span>
      <span class="brand__name">Ridgeline Pet<br>Vision Care</span>
    </div>
  </section>

  <section class="card card--back" aria-label="Business card back">
    <div class="brand brand--back">
      <span class="brand__dot"></span>
      <span class="brand__name">Ridgeline Pet<br>Vision Care</span>
    </div>
  </section>

</main>
</body>
</html>
```